web page design with coding

We are a start up insurance agency who needs to design a full functional web page. we recently did a postcard design though drawkettle I will upload the final project for you to see the color scheme/font we would like to continue to use. I also have a rough draft of verbage I would like our website to have. I will upload that as well.

Reason: I am sorry but the person who will make the final decision on the website is out of the country at the moment and will make the final decision when he returns.

Industry/Entity Type

Insurance

Coding

Coded - Design and coding required

```html
<!DOCTYPE html>
<html lang="en">
<head>
<meta charset="utf-8">
<title>Verity Cover Group — Insurance</title>
<link rel="stylesheet" href="https://fonts.googleapis.com/css2?family=Oswald:wght@300;400&family=Roboto:wght@300;400;500;700&display=swap">
<style>
:root{
  --blue:#3aa8d0;
  --blue-dark:#2d8fb6;
  --blue-line:#2a7fa3;
  --ink:#2b2b2b;
  --text:#555;
  --muted:#8a8a8a;
  --rule:#e3e3e3;
  --pale:#f4f5f6;
  --white:#fff;
}
*{box-sizing:border-box;margin:0;padding:0}
html,body{width:1200px;height:2821px;overflow:hidden}
body{position:relative;background:var(--white);font-family:"Roboto",Arial,sans-serif;color:var(--text)}
.abs{position:absolute}
ul{list-style:none}

/* header */
.site-header{position:absolute;left:0;top:0;width:1200px;height:137px;background:var(--white)}
.brand{position:absolute;left:100px;top:40px;display:flex;align-items:center;gap:12px;font-size:22px;font-weight:500;color:var(--ink)}
.brand-mark{width:40px;height:40px;background:#6b6b6b}
.top-contact{position:absolute;right:100px;top:24px;font-size:13px;color:var(--ink);display:flex;align-items:center;gap:10px}
.top-contact .phone{font-size:17px;font-weight:500}
.top-contact .sep{color:#777;margin:0 6px}
.main-nav{position:absolute;right:86px;top:78px;display:flex;gap:4px}
.main-nav a{display:block;padding:8px 16px;font-size:12px;color:#444;text-decoration:none;letter-spacing:.4px;border:1px solid transparent;border-radius:3px}
.main-nav a.active{border-color:var(--blue);color:var(--blue)}

/* hero */
.hero-photo{position:absolute;left:0;top:137px;width:1200px;height:620px;background:linear-gradient(180deg,#c9cfd0 0%,#d9d6cd 40%,#d7c2a3 75%,#c9ab87 100%)}
.hero-title{position:absolute;left:100px;top:470px;font-family:"Oswald",sans-serif;font-weight:300;font-size:54px;color:#fff;letter-spacing:.3px}
.hero-text{position:absolute;left:100px;top:548px;width:460px;font-size:12px;line-height:20px;color:#3a3a3a}
.btn-dark{position:absolute;left:100px;top:620px;width:122px;height:42px;background:#1f1f1f;color:#fff;font-size:14px;font-weight:700;display:flex;align-items:center;justify-content:center;border-radius:3px}
.hero-dots{position:absolute;left:547px;top:686px;display:flex;gap:10px}
.hero-dots span{width:19px;height:19px;border-radius:50%;border:2px solid #fff}
.hero-dots span.on{background:#fff}

/* welcome */
.welcome-title{position:absolute;left:0;width:1200px;top:796px;text-align:center;font-size:26px;font-weight:700;color:var(--ink)}
.welcome-sub{position:absolute;left:0;width:1200px;top:832px;text-align:center;font-size:27px;font-weight:300;color:var(--ink)}
.welcome-text{position:absolute;left:130px;width:940px;top:880px;text-align:center;font-size:11.5px;line-height:20px;color:#666}
.btn-blue{position:absolute;height:36px;background:var(--blue);color:#fff;font-size:11px;font-weight:500;display:flex;align-items:center;justify-content:center;border-radius:3px;letter-spacing:.3px}

/* insurance cards */
.card-photo{position:absolute;top:1063px;width:466px;height:277px;border:4px solid #eee}
.card-photo.business{left:100px;background:linear-gradient(135deg,#c8a98a,#e6d6c6 45%,#6c6f7a)}
.card-photo.personal{left:632px;background:linear-gradient(135deg,#a5753f,#c89a62 50%,#e9e6e0)}
.divider{position:absolute;left:600px;top:1063px;width:1px;height:702px;background:var(--rule)}
.card-title{position:absolute;top:1362px;font-size:22px;font-weight:400;color:var(--ink)}
.card-text{position:absolute;top:1398px;width:466px;font-size:11px;line-height:17px;color:#777}
.cover-list{position:absolute;font-size:12.5px;line-height:27.5px;color:#444}
.cover-list li{position:relative;padding-left:20px}
.cover-list li::before{content:"";position:absolute;left:0;top:8px;width:9px;height:9px;border:2px solid var(--blue);border-radius:2px}
.cover-list li::after{content:"";position:absolute;left:5px;top:7px;width:4px;height:8px;border-right:2px solid var(--blue);border-bottom:2px solid var(--blue);transform:rotate(40deg)}
.cover-list li.wrap{line-height:17px;padding-top:5px}

/* about */
.about-band{position:absolute;left:0;top:1809px;width:1200px;height:373px;background:linear-gradient(90deg,#1f4456 0%,#3d6677 45%,#6d8d98 100%)}
.about-title{position:absolute;left:100px;top:1858px;font-size:26px;color:#fff}
.about-text{position:absolute;left:100px;top:1902px;width:600px;font-size:11.5px;line-height:19px;color:#eef4f6}
.quote-form{position:absolute;left:858px;top:1842px;width:242px;height:304px;background:#fff;border-radius:3px;box-shadow:0 2px 6px rgba(0,0,0,.2)}
.quote-form h3{height:43px;background:var(--blue);color:#fff;font-weight:400;font-size:17px;display:flex;align-items:center;justify-content:center;border-radius:3px 3px 0 0}
.field{position:absolute;left:15px;width:212px;height:34px;border:1px solid #d5d5d5;border-radius:3px;font-size:11px;color:#aaa;padding:10px 8px}
.form-label{position:absolute;left:15px;top:212px;font-size:11px;color:var(--blue)}
.check{position:absolute;top:234px;font-size:11px;color:#444;display:flex;align-items:center;gap:6px}
.check span{width:10px;height:10px;border:1px solid #888}

/* testimonials */
.testimonials{position:absolute;left:0;top:2182px;width:1200px;height:340px;background:var(--pale)}
.section-title{position:absolute;left:0;width:1200px;top:2236px;text-align:center;font-size:26px;font-weight:300;color:var(--ink)}
.portrait{position:absolute;left:182px;top:2287px;width:170px;height:170px;border-radius:50%;background:radial-gradient(circle at 50% 40%,#b7a291,#5c5f66 70%);border:4px solid #fff}
.quote-mark{position:absolute;font-family:Georgia,serif;font-size:80px;line-height:1;color:var(--blue)}
.quote-text{position:absolute;left:440px;top:2312px;width:620px;font-size:12.5px;line-height:21px;color:#555}
.author{position:absolute;left:440px;top:2396px;font-size:15px;font-weight:500;color:var(--ink)}
.author-loc{position:absolute;left:440px;top:2419px;font-size:10px;color:#aaa}
.slider-bars{position:absolute;left:437px;top:2451px;display:flex;gap:12px}
.slider-bars span{width:22px;height:5px;background:#bbb}
.slider-bars span.on{background:var(--blue)}

/* footer */
.footer-bg{position:absolute;left:0;top:2470px;width:1200px;height:351px}
.footer-base{position:absolute;left:0;top:2762px;width:1200px;height:59px;background:var(--blue-dark)}
.f-head{position:absolute;top:2578px;font-size:17px;font-weight:500;color:#fff;letter-spacing:.3px}
.f-rule{position:absolute;top:2575px;width:1px;height:170px;background:rgba(255,255,255,.35)}
.badge{position:absolute;width:118px;height:51px;border:2px solid #fff}
.f-links{position:absolute;left:489px;top:2628px;font-size:12px;line-height:23.5px;color:#fff}
.f-contact{position:absolute;left:690px;top:2628px;font-size:12px;line-height:24px;color:#fff}
.f-contact .ico{display:inline-block;width:14px;margin-right:8px}
.f-social{position:absolute;left:999px;top:2634px;font-size:12px;line-height:24px;color:#fff}
.f-social li{display:flex;align-items:center;gap:12px}
.f-social li span{width:9px;height:9px;border-radius:50%;background:#fff}
.copyright{position:absolute;left:0;width:1200px;top:2782px;text-align:center;font-size:11px;color:#eaf6fb}
</style>
</head>
<body>

<header class="site-header">
  <div class="brand"><span class="brand-mark"></span>Verity Cover Group</div>
  <div class="top-contact">
    <svg width="14" height="11" viewBox="0 0 14 11"><rect x="0.5" y="0.5" width="13" height="10" fill="var(--blue)"/><path d="M1 1 L7 6 L13 1" stroke="#fff" fill="none"/></svg>
    <span>info@veritycover.net</span><span class="sep">/</span>
    <svg width="13" height="13" viewBox="0 0 24 24"><path fill="var(--blue)" d="M6.6 10.8a15 15 0 0 0 6.6 6.6l2.2-2.2c.3-.3.7-.4 1-.2 1.1.4 2.300.6 3.6.6.6 0 1 .4 1 1V20c0 .6-.4 1-1 1A17 17 0 0 1 3 4c0-.6.4-1 1-1h3.5c.6 0 1 .4 1 1 0 1.3.2 2.5.6 3.6.1.3 0 .7-.2 1z"/></svg>
    <span class="phone">+1 805 555 0142</span>
  </div>
  <nav class="main-nav">
    <a class="active">HOME</a><a>INSURANCE</a><a>ABOUT US</a><a>SERVICES</a><a>CONTACT</a>
  </nav>
</header>

<div class="hero-photo" role="img" aria-label="Family of four walking hand in hand along a sunlit beach"></div>
<h1 class="hero-title">Verity Cover Group</h1>
<p class="hero-text">Verity Cover Group is committed to providing the best risk management solutions to fit each client's unique needs. This includes providing creative solutions as if we were seeking insurance for our own family.</p>
<div class="btn-dark">CLICK HERE</div>
<div class="hero-dots"><span></span><span class="on"></span><span></span><span></span></div>

<svg class="abs" style="left:0;top:690px" width="1200" height="80" viewBox="0 0 1200 80">
  <path d="M0 40 C200 62 420 40 520 30 C560 26 580 14 600 14 C620 14 640 26 680 30 C780 40 1000 62 1200 40 L1200 80 L0 80Z" fill="#fff"/>
  <path d="M0 40 C200 62 420 40 520 30 C560 26 580 14 600 14 C620 14 640 26 680 30 C780 40 1000 62 1200 40" fill="none" stroke="#5b9bb4" stroke-width="7"/>
</svg>

<h2 class="welcome-title">Welcome!</h2>
<p class="welcome-sub">Verity Cover Group</p>
<p class="welcome-text">At Verity Cover Group We Work For You. We can help ensure you have Coverage You need to protect your family's assets if the unexpected happens. What sets us apart? With over 2 years of combined experience, and as a Steady Shield Independent insurance agent we are aware of particular risks and frustrations You encounter when purchasing insurance. We meet the Needs of Clients at every level. Trust one of our agents who are always available to assist and guide you at every step of the way. You are our primary Concern, protection For Today, Tomorrow and the Unknown.</p>
<div class="btn-blue" style="left:549px;top:986px;width:102px">READ MORE</div>

<div class="card-photo business" role="img" aria-label="Agent reviewing a business policy folder with a couple at a desk"></div>
<div class="card-photo personal" role="img" aria-label="Desk with laptop, glasses, stethoscope and a life insurance form"></div>
<div class="divider"></div>

<h3 class="card-title" style="left:100px">Business Insurance</h3>
<p class="card-text" style="left:100px">Verity Cover Group can help you take steps to protect your business and your family from the financial consequences of events that could disrupt operations, reduce profits, or even cause the business to go bankrupt.</p>
<ul class="cover-list" style="left:100px;top:1473px">
  <li>Bond</li><li>Builders Risk</li><li>Business Owners Policy (BOP)</li><li>Commercial Auto</li><li>Crime</li><li>Crop / Hail</li><li>Difference in Conditions</li><li>Directors and Officers (D&amp;O)</li><li>Employment Practices Liability</li><li>Errors &amp; Omissions (E&amp;O)</li><li>Equipment Breakdown</li>
</ul>
<ul class="cover-list" style="left:365px;top:1473px">
  <li>Garage</li><li>General Liability</li><li>Inland Marine</li><li>Liquor Liability</li><li>Medical Malpractice</li><li>Professional Liability</li><li>Property</li><li>Truckers</li><li>Umbrella</li><li class="wrap">Workers Compensation /<br>Employer Liability</li>
</ul>

<h3 class="card-title" style="left:632px">Personal Insurance</h3>
<p class="card-text" style="left:632px">Verity Cover Group can help you take steps to protect your business and your family from the financial consequences of events that could disrupt operations, reduce profits, or even cause the business to go bankrupt.</p>
<ul class="cover-list" style="left:632px;top:1473px">
  <li>Auto</li><li>Boat &amp; Marine</li><li>Collector Car</li><li>Condo</li><li>Flood</li><li>High Net Worth</li><li>Homeowners</li><li>Rental and Investment Property</li><li>Mobile Home</li><li>Motor Home</li>
</ul>
<ul class="cover-list" style="left:897px;top:1486px">
  <li>Motorcycle</li><li>Personal Umbrella</li><li>Recreational Vehicles</li><li>Renters</li><li>Travel</li><li>Valuable Items</li>
</ul>

<section class="about-band" role="img" aria-label="Many raised hands giving a thumbs up against a blue sky"></section>
<h2 class="about-title">About Us</h2>
<div class="about-text">
  <p>Established in 2015, Verity Cover Group is a full service independent insurance agency. Our licensed agents have the experience to custom tailor a program to meet your specific needs &amp; our professional support staff will provide you with top notch customer service to help ease the burden of managing your insurance program. We have established relationships with carriers in order to offer you the most competitive products and services available in the marketplace today.</p>
  <p style="margin-top:18px">Verity Cover Group is committed to providing the best risk management solutions to fit each client's unique needs. This includes providing creative solutions as if we were seeking insurance for our own family.</p>
</div>
<div class="btn-blue" style="left:100px;top:2088px;width:101px;height:34px">READ MORE</div>

<form class="quote-form">
  <h3>INSURANCE QUOTES</h3>
  <div class="field" style="top:71px">Name *</div>
  <div class="field" style="top:116px">email *</div>
  <div class="field" style="top:161px">Phone *</div>
  <div class="form-label">Select type of Insurance</div>
  <div class="check" style="left:15px"><span></span>Business</div>
  <div class="check" style="left:100px"><span></span>Personal</div>
  <div class="btn-blue" style="left:79px;top:259px;width:83px;height:30px;font-size:10px">GO TO STEP2</div>
</form>

<section class="testimonials"></section>
<h2 class="section-title">What people Says</h2>
<div class="portrait" role="img" aria-label="Portrait photo of a client in a suit"></div>
<div class="quote-mark" style="left:398px;top:2296px">&ldquo;</div>
<p class="quote-text">Mistaken idea of denouncing pleasure and praising pain was born and I will give you a complete account of the system, and expound the actual teachings of the great explorer of the truth, the master-builder human happiness. No one rejects, dislikes, or avoids pleasure itself, because it is pleasure, but because those</p>
<div class="quote-mark" style="left:1052px;top:2348px">&rdquo;</div>
<div class="author">Author Name</div>
<div class="author-loc">City Location</div>
<div class="slider-bars"><span></span><span class="on"></span><span></span></div>

<svg class="footer-bg" width="1200" height="351" viewBox="0 0 1200 351">
  <path d="M0 20 C200 48 420 28 520 14 C560 8 580 0 600 0 C620 0 640 8 680 14 C780 28 1000 48 1200 20 L1200 351 L0 351Z" fill="var(--blue)"/>
  <path d="M0 20 C200 48 420 28 520 14 C560 8 580 0 600 0 C620 0 640 8 680 14 C780 28 1000 48 1200 20" fill="none" stroke="var(--blue-line)" stroke-width="7"/>
</svg>
<div class="footer-base"></div>

<h4 class="f-head" style="left:100px">CUSTOMERS</h4>
<div class="badge" style="left:100px;top:2626px"></div>
<div class="badge" style="left:241px;top:2626px"></div>
<div class="badge" style="left:100px;top:2684px"></div>
<div class="badge" style="left:241px;top:2684px"></div>
<div class="f-rule" style="left:423px"></div>

<h4 class="f-head" style="left:489px">OUR LINK</h4>
<ul class="f-links"><li>Home</li><li>About Us</li><li>Services</li><li>Contact</li></ul>
<div class="f-rule" style="left:636px"></div>

<h4 class="f-head" style="left:690px">CONTACT US</h4>
<div class="f-contact">
  <p>2150 Palm Crest Ave Suite 410 Coral Bay,<br>FL 33190</p>
  <p><span class="ico"><svg width="13" height="10" viewBox="0 0 14 11"><rect x=".5" y=".5" width="13" height="10" fill="#fff"/><path d="M1 1 L7 6 L13 1" stroke="var(--blue)" fill="none"/></svg></span>hello@veritycover.net</p>
  <p><span class="ico"><svg width="12" height="12" viewBox="0 0 24 24"><path fill="#fff" d="M6.6 10.8a15 15 0 0 0 6.6 6.6l2.2-2.2c.3-.3.7-.4 1-.2 1.1.4 2.3.6 3.6.6.6 0 1 .4 1 1V20c0 .6-.4 1-1 1A17 17 0 0 1 3 4c0-.6.4-1 1-1h3.5c.6 0 1 .4 1 1 0 1.3.2 2.5.6 3.6.1.3 0 .7-.2 1z"/></svg></span>(786) 555-0193</p>
</div>
<div class="f-rule" style="left:940px"></div>

<h4 class="f-head" style="left:999px">FOLLOW US</h4>
<ul class="f-social"><li><span></span>Friendpage</li><li><span></span>Chirper</li><li><span></span>Viewtube</li></ul>

<p class="copyright">&copy; 2015 - 2016. Verity Cover Group. All Rights Reserved.</p>

</body>
</html>
```